Awesome design needed for standup comedy portal

We need a website designed for a new portal (grinbox.net) dedicated to standup comedy.

- homepage
- featured "hero" content at top
- banner advertising
- browse comics
- browse venues
- search
- signup / login
- social media links

- comic page
- name
- pictures
- calendar of performances
- list of albums (with buy buttons)
- list of specials (Vexora, Plumtrack, etc. with buy buttons)
- reviews
- latest tweets
- latests pixaloop photos
- links to social media accounts
- links to filmdex, podcast

- venue page
- name
- pictures
- address, phone number
- calendar of events
- reviews
- latest tweets
- links to filmdex, podcast

Target Market(s)

Fans of standup comedy and comedians

Number of Pages Required

Font styles to use
Sans Serif

Requirements
Must have
• Will eventually be implemented in bootstrap, so please keep that in mind

```html
<!DOCTYPE html>
<html lang="en">
<head>
<meta charset="utf-8">
<title>Grinbox – Stand-up Comedy Portal</title>
<link href="https://fonts.googleapis.com/css2?family=Luckiest+Guy&family=Mulish:wght@400;600;700&display=swap" rel="stylesheet">
<style>
:root{
  --red:#c8383f;
  --red-dark:#b42c33;
  --tan:#e8bd8f;
  --orange:#ec7e48;
  --green:#8fcb45;
  --teal:#3cc0aa;
  --ink:#2b2b2b;
  --grey:#f7f7f7;
  --line:#e6e6e6;
  --white:#ffffff;
}
*{box-sizing:border-box;margin:0;padding:0}
html,body{width:1200px;height:2707px;overflow:hidden}
body{position:relative;background:var(--white);font-family:"Mulish",sans-serif;color:var(--ink)}
.abs{position:absolute}
.display{font-family:"Luckiest Guy","Mulish",sans-serif;font-weight:400;letter-spacing:1px}

/* header */
.site-header{left:0;top:0;width:1200px;height:112px;background:var(--white)}
.brand{left:135px;top:30px;display:flex;align-items:center;gap:12px}
.brand-dot{width:44px;height:44px;border-radius:50%;background:var(--red)}
.brand-name{font-weight:700;font-size:34px;color:var(--red)}
.main-nav a{position:absolute;top:52px;font-size:15px;color:var(--ink);text-decoration:none}
.main-nav a.active{color:var(--red);border-bottom:2px solid var(--red);padding-bottom:8px}
.btn-pill{position:absolute;top:47px;height:32px;border-radius:16px;font-size:15px;display:flex;align-items:center;justify-content:center;text-decoration:none}
.btn-signup{left:888px;width:87px;border:1px solid var(--line);color:var(--ink)}
.btn-login{left:984px;width:83px;background:var(--red);color:var(--white)}

/* hero */
.hero{left:0;top:112px;width:1200px;height:570px;overflow:hidden}
.hero-photo{width:100%;height:100%;background:
  radial-gradient(ellipse 260px 230px at 420px 330px,#c9a146 0%,#a9782a 55%,transparent 70%),
  radial-gradient(ellipse 200px 150px at 760px 160px,#3aa34a 0%,#d7c23a 40%,transparent 70%),
  linear-gradient(90deg,#7a0f12,#b3191d 30%,#8c1216 60%,#b01a1e 100%)}
.hero-card{left:827px;top:180px;width:242px;height:249px;border-radius:22px;background:rgba(255,255,255,.82);text-align:center;padding:20px 22px}
.hero-card h2{color:var(--red);font-size:38px;line-height:44px}
.hero-card p{font-size:13px;line-height:18px;color:#555;margin-top:8px}
.hero-card a{display:block;margin:16px auto 0;width:196px;height:44px;border-radius:22px;background:var(--red);color:var(--white);font-size:17px;font-weight:600;line-height:44px;text-decoration:none}
.slider-dots{left:565px;top:463px;display:flex;gap:4px}
.slider-dots span{width:16px;height:16px;border-radius:50%;background:var(--white)}
.slider-dots span.current{background:transparent;border:2px solid var(--white)}
.hero-curve{left:0;top:640px}

/* welcome */
.welcome{left:0;top:672px;width:1200px;height:369px;background:var(--red);color:var(--white)}
.welcome-photo{left:137px;top:46px;width:260px;height:260px;border-radius:50%;border:5px solid var(--white);background:linear-gradient(160deg,#9aa3ab,#6c5a55 50%,#3a4a6a)}
.welcome h1{position:absolute;left:457px;top:48px;font-size:36px;line-height:44px}
.welcome p{position:absolute;left:457px;width:610px;font-size:13px;line-height:21px}
.btn-outline{left:457px;top:252px;width:189px;height:47px;border:1px solid rgba(255,255,255,.6);border-radius:24px;font-size:17px;display:flex;align-items:center;justify-content:center;letter-spacing:.5px}

/* search band */
.search-band{left:0;top:1041px;width:1200px;height:136px;background:var(--tan)}
.search-field{top:49px;width:422px;height:40px;border-radius:20px;background:var(--white);display:flex;align-items:center;justify-content:space-between;padding:0 24px 0 27px;font-size:14px;color:#aaa}

/* shows */
.section-title{font-size:34px;line-height:40px;text-transform:uppercase;color:var(--ink)}
.shows-title{left:134px;top:1236px}
.shows-rule{left:134px;top:1296px;width:934px;height:1px;background:var(--line)}
.show-card{top:1343px;width:283px;height:359px;border-radius:26px;color:var(--white);text-align:center;padding:20px}
.show-card.orange{left:134px;background:var(--orange)}
.show-card.green{left:458px;background:var(--green)}
.show-card.teal{left:783px;background:var(--teal)}
.show-photo{height:153px;border-radius:22px}
.show-card h3{font-weight:400;font-size:17px;margin-top:16px}
.show-card p{font-size:12px;line-height:16px;margin-top:8px;padding:0 8px}
.show-date{display:block;font-size:12px;margin-top:6px}
.show-card a{display:block;margin:14px auto 0;width:150px;height:36px;border-radius:18px;background:var(--white);color:#444;font-size:17px;line-height:36px;text-decoration:none}

/* video */
.video-section{left:0;top:1796px;width:1200px;height:551px;background:var(--grey)}
.video-title{left:0;top:48px;width:1200px;text-align:center}
.video-frame{left:132px;top:125px;width:936px;height:359px;border:2px solid #ddd;background:var(--white);padding:10px}
.video-still{width:100%;height:100%;background:linear-gradient(180deg,#1d2530,#46362f 45%,#2a2422 75%,#111)}
.play-btn{left:424px;top:137px}

/* footer */
.site-footer{left:0;top:2347px;width:1200px;height:288px;background:var(--red);color:var(--white)}
.footer-heading{position:absolute;top:48px;font-weight:400;font-size:22px}
.footer-item{position:absolute;font-size:13px;color:var(--white);text-decoration:none;white-space:nowrap}
.footer-divider{top:36px;width:1px;height:215px;background:rgba(255,255,255,.15)}
.newsletter{left:776px;top:90px;width:293px;height:36px;background:var(--white);display:flex;align-items:center;padding:4px}
.newsletter-placeholder{flex:1;font-size:12px;color:#aaa;padding-left:10px;letter-spacing:.5px}
.newsletter-button{background:var(--red-dark);color:var(--white);font-size:11px;font-weight:700;padding:7px 10px;letter-spacing:.3px}
.social{top:143px;width:30px;height:30px;border-radius:50%;background:var(--red-dark);display:flex;align-items:center;justify-content:center}

/* bottom bar */
.bottom-bar{left:0;top:2635px;width:1200px;height:72px;background:var(--white);font-size:12px;color:#555}
.bottom-bar span{position:absolute;top:29px}
</style>
</head>
<body>

<header class="site-header abs">
  <div class="brand abs"><span class="brand-dot"></span><span class="brand-name">Grinbox</span></div>
  <nav class="main-nav">
    <a class="active" style="left:397px">Home</a>
    <a style="left:473px">About Us</a>
    <a style="left:570px">Browse Comics</a>
    <a style="left:708px">Venues</a>
    <a style="left:790px">Contact Us</a>
  </nav>
  <a class="btn-pill btn-signup">Signup</a>
  <a class="btn-pill btn-login">Login</a>
</header>

<section class="hero abs">
  <div class="hero-photo" role="img" aria-label="Performer holding golden theatre masks in front of a red stage curtain"></div>
  <div class="hero-card abs">
    <h2 class="display">Grinbox</h2>
    <p>Sed ut perspiciatis unde omnis iste natus error sit voluptatem accusantium doloremque laudantium</p>
    <a>MORE INFO</a>
  </div>
  <div class="slider-dots abs"><span class="current"></span><span></span><span></span><span></span></div>
</section>

<svg class="hero-curve abs" width="1200" height="40" viewBox="0 0 1200 40">
  <path d="M0 32 Q600 -12 1200 32 L1200 40 L0 40 Z" fill="#c8383f"/>
  <path d="M0 32 Q600 -12 1200 32" fill="none" stroke="#fff" stroke-width="4"/>
</svg>

<section class="welcome abs">
  <div class="welcome-photo abs" role="img" aria-label="Street parade with costumed giant-head figures"></div>
  <h1 class="display">Welcome to Grinbox</h1>
  <p style="top:108px">Duis aute irure dolor in reprehenderit in voluptate velit esse cillum dolore eu fugiat nulla pariatur. Excepteur sint occaecat cupidatat non proident, sunt in culpa qui officia deserunt mollit anim id est laborum labore et dolore magna.</p>
  <p style="top:178px">Sed ut perspiciatis unde omnis iste natus error sit voluptatem accusantium doloremque laudantium, totam rem aperiam, eaque ipsa.</p>
  <div class="btn-outline abs">GET A QUOTE</div>
</section>

<section class="search-band abs">
  <div class="search-field abs" style="left:157px">Browse comics
    <svg width="14" height="14" viewBox="0 0 14 14"><circle cx="6" cy="6" r="4.5" fill="none" stroke="#c8383f" stroke-width="1.5"/><path d="M9.5 9.5 13 13" stroke="#c8383f" stroke-width="1.5"/></svg></div>
  <div class="search-field abs" style="left:621px">Browse venues
    <svg width="14" height="14" viewBox="0 0 14 14"><circle cx="6" cy="6" r="4.5" fill="none" stroke="#c8383f" stroke-width="1.5"/><path d="M9.5 9.5 13 13" stroke="#c8383f" stroke-width="1.5"/></svg></div>
</section>

<h2 class="section-title display shows-title abs">Upcoming Shows</h2>
<div class="shows-rule abs"></div>

<article class="show-card orange abs">
  <div class="show-photo" role="img" aria-label="Clown performer with two audience members" style="background:linear-gradient(135deg,#d9b98a,#3d4a8a 55%,#c44)"></div>
  <h3>Show Tittle here</h3>
  <p>Sed ut perspiciatis unde omnis iste natus error sit voluptatem accusantium doloremque laudantium.</p>
  <span class="show-date">15 Feb 2016</span>
  <a>More Info</a>
</article>
<article class="show-card green abs">
  <div class="show-photo" role="img" aria-label="Street performer in front of a crowd" style="background:linear-gradient(180deg,#b9a58a,#8a7a66 50%,#5c4e48)"></div>
  <h3>Show Tittle here</h3>
  <p>Sed ut perspiciatis unde omnis iste natus error sit voluptatem accusantium doloremque laudantium.</p>
  <span class="show-date">14 April 2016</span>
  <a>More Info</a>
</article>
<article class="show-card teal abs">
  <div class="show-photo" role="img" aria-label="Masked performer in a red shirt on stage" style="background:linear-gradient(135deg,#6b5a4a,#c33 50%,#e8e0d8)"></div>
  <h3>Show Tittle here</h3>
  <p>Sed ut perspiciatis unde omnis iste natus error sit voluptatem accusantium doloremque laudantium.</p>
  <span class="show-date">18 March 2016</span>
  <a>More Info</a>
</article>

<section class="video-section abs">
  <h2 class="section-title display video-title abs">Watch My Video</h2>
  <div class="video-frame abs">
    <div class="video-still" role="img" aria-label="Television studio set with cameras and crew"></div>
    <svg class="play-btn abs" width="80" height="80" viewBox="0 0 80 80">
      <circle cx="40" cy="40" r="36" fill="none" stroke="rgba(255,255,255,.75)" stroke-width="4"/>
      <path d="M32 24 L56 40 L32 56 Z" fill="rgba(255,255,255,.75)"/>
    </svg>
  </div>
</section>

<footer class="site-footer abs">
  <h4 class="footer-heading" style="left:134px">Quick Links</h4>
  <a class="footer-item" style="left:134px;top:108px">Home</a>
  <a class="footer-item" style="left:134px;top:135px">About Us</a>
  <a class="footer-item" style="left:134px;top:162px">Browse Comics</a>
  <a class="footer-item" style="left:134px;top:189px">Venues</a>
  <a class="footer-item" style="left:308px;top:108px">Log In</a>
  <a class="footer-item" style="left:308px;top:135px">Privacy Policy</a>
  <a class="footer-item" style="left:308px;top:162px">FAQs</a>

  <div class="footer-divider abs" style="left:435px"></div>

  <h4 class="footer-heading" style="left:486px">Contact Us</h4>
  <span class="footer-item" style="left:486px;top:100px">Grinbox, Street Name,</span>
  <span class="footer-item" style="left:486px;top:126px">City Address, Country, Pin Code.</span>
  <svg class="abs" style="left:488px;top:156px" width="14" height="14" viewBox="0 0 14 14"><path d="M3 1 L5.5 1 L6.5 4 L5 5.5 Q6.5 8.5 8.5 9 L10 7.5 L13 8.5 L13 11 Q12 13 10 13 Q1 11 1 3 Q1 1 3 1Z" fill="#fff"/></svg>
  <span class="footer-item" style="left:514px;top:156px">+1-234-567-8900</span>
  <svg class="abs" style="left:488px;top:184px" width="14" height="11" viewBox="0 0 14 11"><rect width="14" height="11" rx="1" fill="#fff"/><path d="M1 1 L7 6 L13 1" fill="none" stroke="#c8383f" stroke-width="1.3"/></svg>
  <span class="footer-item" style="left:514px;top:181px">info@grinbox.net</span>

  <div class="footer-divider abs" style="left:738px"></div>

  <h4 class="footer-heading" style="left:776px">Join Newsletters</h4>
  <div class="newsletter abs"><span class="newsletter-placeholder">EMAIL ADDRESS</span><span class="newsletter-button">SUBSCRIBE</span></div>
  <a class="social abs" style="left:776px" aria-label="Social link one"><svg width="12" height="12" viewBox="0 0 12 12"><path d="M2 10 L10 2 M4 2 H10 V8" fill="none" stroke="#fff" stroke-width="1.8"/></svg></a>
  <a class="social abs" style="left:817px" aria-label="Social link two"><svg width="12" height="12" viewBox="0 0 12 12"><path d="M2 10 L10 2 M4 2 H10 V8" fill="none" stroke="#fff" stroke-width="1.8"/></svg></a>
  <a class="social abs" style="left:860px" aria-label="Social link three"><svg width="12" height="12" viewBox="0 0 12 12"><path d="M2 10 L10 2 M4 2 H10 V8" fill="none" stroke="#fff" stroke-width="1.8"/></svg></a>
  <a class="social abs" style="left:902px" aria-label="Social link four"><svg width="12" height="12" viewBox="0 0 12 12"><path d="M2 10 L10 2 M4 2 H10 V8" fill="none" stroke="#fff" stroke-width="1.8"/></svg></a>
  <a class="social abs" style="left:943px" aria-label="Social link five"><svg width="12" height="12" viewBox="0 0 12 12"><path d="M2 10 L10 2 M4 2 H10 V8" fill="none" stroke="#fff" stroke-width="1.8"/></svg></a>
</footer>

<div class="bottom-bar abs">
  <span style="left:134px">© 2017 Grinbox.&nbsp; All right reserved.&nbsp; Term of Use</span>
  <span style="left:879px;font-size:11px">Terms &amp; Conditions</span>
  <span style="left:984px;color:#ccc">|</span>
  <span style="left:1000px;font-size:11px">Privacy Policy</span>
</div>

</body>
</html>
```